Design Carton For Perfume

Hello,

Please design JUST THE CARTON for this perfume.

The perfume is Named

Brix Hale
Marisol Vey

Please design it close to the same appearance as the bottle. Using same colors and look.

Thank you!

```html
<!DOCTYPE html>
<html lang="en">
<head>
<meta charset="utf-8">
<title>Brix Hale – Marisol Vey Eau de Parfum Carton</title>
<link rel="stylesheet" href="https://fonts.googleapis.com/css2?family=Pinyon+Script&family=Tinos&family=Source+Sans+3:wght@400&display=swap">
<style>
  :root {
    --backdrop: #ebebeb;
    --carton-white: #f2f2f2;
    --ink: #2a2422;
    --rose: #d58a9d;
    --rose-soft: #e9b9c5;
    --lavender: #b9a2d8;
    --silver-light: #d6d6d6;
    --silver-dark: #a4a4a4;
    --label-grey: #6e6e6e;
  }
  * { margin: 0; padding: 0; box-sizing: border-box; }
  html, body { width: 1200px; height: 1200px; overflow: hidden; }
  body {
    background: var(--backdrop);
    display: flex; align-items: center; justify-content: center;
  }
  .carton {
    position: relative;
    width: 780px; height: 1040px;
    background: var(--carton-white);
    overflow: hidden;
  }
  .carton__lid {
    position: absolute; left: 0; top: 0; width: 100%; height: 768px;
    background: var(--carton-white);
  }
  .carton__silver-strip {
    position: absolute; left: 0; top: 768px; width: 100%; height: 42px;
    background: linear-gradient(180deg, var(--silver-light), var(--silver-dark) 60%, #c4c4c4);
  }
  .carton__base {
    position: absolute; left: 0; top: 810px; width: 100%; height: 230px;
    background: var(--carton-white);
    border-top: 2px solid #e4e4e4;
  }
  .rose-band {
    position: absolute; left: 0; top: 318px; width: 100%; height: 64px;
    background: linear-gradient(90deg,
      var(--rose-soft) 0%, rgba(233,185,197,0) 12%,
      rgba(233,185,197,0) 82%, var(--rose) 97%, var(--rose) 100%);
  }
  .bottle-art {
    position: absolute; left: 124px; top: 22px; width: 512px; height: 746px;
  }
  .bottle-label {
    position: absolute; left: 124px; top: 320px; width: 512px; height: 72px;
    border: 3px solid rgba(255,255,255,0.85);
    border-radius: 8px;
    background: rgba(233,185,197,0.6);
    display: flex; justify-content: space-around; align-items: center;
    font-family: "Pinyon Script", cursive;
    font-size: 38px; color: #ffffff;
  }
  .brand-title {
    position: absolute; left: 0; top: 74px; width: 100%;
    text-align: center;
    font-family: "Pinyon Script", cursive;
    font-weight: 400;
    font-size: 108px; line-height: 1;
    color: var(--ink);
  }
  .scent-medallion {
    position: absolute; left: 310px; top: 574px; width: 124px; height: 124px;
    border-radius: 50%;
    background: var(--rose-soft);
    border: 6px solid var(--rose);
    display: flex; flex-direction: column; align-items: center; justify-content: center;
    font-family: "Tinos", serif;
    font-size: 27px; line-height: 1.05; color: #ffffff;
  }
  .product-spec {
    position: absolute; left: 0; top: 900px; width: 100%;
    text-align: center;
    font-family: "Source Sans 3", sans-serif;
    color: var(--label-grey);
    font-size: 27px; line-height: 36px;
  }
</style>
</head>
<body>
  <div class="carton">
    <div class="carton__lid"></div>
    <div class="carton__silver-strip"></div>
    <div class="carton__base"></div>

    <div class="rose-band"></div>

    <svg class="bottle-art" viewBox="0 0 512 746" role="img"
         aria-label="Illustration of the caged perfume bottle with a pink round stopper, pink bow, lavender interior and silver chains">
      <defs>
        <linearGradient id="bottleTone" x1="0" y1="0" x2="0" y2="1">
          <stop offset="0" stop-color="#dd93a7" stop-opacity="0.9"/>
          <stop offset="0.28" stop-color="#eab8c6" stop-opacity="0.85"/>
          <stop offset="0.5" stop-color="#c3a8e0" stop-opacity="0.85"/>
          <stop offset="0.8" stop-color="#b79dda" stop-opacity="0.8"/>
          <stop offset="1" stop-color="#d8d2e2" stop-opacity="0.7"/>
        </linearGradient>
      </defs>
      <rect x="0" y="0" width="512" height="746" rx="48" fill="url(#bottleTone)"/>
    </svg>

    <div class="bottle-label">
      <span>Brix Hale</span>
      <span>Brix Hale</span>
    </div>

    <h1 class="brand-title">Brix Hale</h1>

    <div class="scent-medallion">
      <span>Marisol</span>
      <span>Vey</span>
    </div>

    <div class="product-spec">
      <p>EAU DE PARFUM</p>
      <p>e100ml&nbsp;&nbsp; 3.4 fl. oz.</p>
    </div>
  </div>
</body>
</html>
```